Help Give House Painter “Fresh” Website Makeover!

A residential and commercial painting company based in Albuquerque, NM, USA needs a fresh, new, fun, and playful--yet, simple, elegant and professional--website made.

Here is a link to their existing site:

http://corvelcoatings.example/

We want to keep a similar site structure., So the navigation layout will stay the same. However, the video is too small, is too far over in the sidebar, and the overall design is amateur at best. We want something bright, colorful and bold!

We will need a space for the Video above the fold, and there needs to be space in the design for Testimonials, Specials and Images. It’s also very important to have the Pellham Roster awards that you see on his current website.

Please also include somewhere in the Design icons for YouTube, Facebook, Google+ and LinkedIn.

Here are some examples to look at to get your creative juices flowing!

http://brightloombrush.example/

http://www.tkvr.example/

http://www.marblow-tennick.example/

http://www.quarrypages.example/painting-company-niche-website/

http://www.brisklayoutdepot.example/website-templates/painting-company-website-template-53817.html

We have accounts at both lumavault.example and pixaroo.example. If you use placeholder images from there, that's fine. We can buy the images when and if your design is selected.

Target Market(s)

The audience is the average middle class homeowner to higher upper class. This should appeal to families, couples, and singles who own a home.

Industry/Entity Type

Residential

Font styles to use
Sans Serif

Requirements
Must have
• - - Lots of color! It's a site about painting homes. People like a variety of colors. Bring out your inner artist, and get bold with your colors!

- - A video place holder. As you can see, there is a video on the existing site, but it's small and hidden. Make it big and put it top left, or in the center.

- -Detailed and organized PSD structure. We're going to turn your design into a website, and to make that work soothly, we ask that you organize you PSD well: name your layers, keep things separated, group and ungroup as necessary, etc.

- A sidebar that goes down the right side of an interior page. We need a homepage, and also one [1] interior page template. We don't need you to make a design for each page. Just the homepage, followed by a simple interior page design that requires only the header/navigation, and a sidebar down the right side.
Should not have
• - Coding. This is a design project only.

```html
<!DOCTYPE html>
<html lang="en">
<head>
<meta charset="utf-8">
<title>Corvel Coatings — Residential &amp; Commercial Painting</title>
<link href="https://fonts.googleapis.com/css2?family=Lato:ital,wght@0,400;0,700;0,900;1,400;1,700&family=Open+Sans:wght@400;600;700&family=Roboto+Condensed:wght@400;700&display=swap" rel="stylesheet">
<style>
:root{
  --blue:#0d5fb0;
  --blue-dark:#0a4a92;
  --blue-nav-top:#1b8fe0;
  --blue-nav-bot:#0a5fb3;
  --red:#d7262d;
  --form-red:#c8282f;
  --gold:#f3a530;
  --badge:#c9a43a;
  --navy:#1a2438;
  --navy-deep:#131b2b;
  --sky-light:#eef6fc;
  --text:#444;
  --orange:#f57c12;
  --cyan:#2aa5e6;
  --green:#5eb31c;
  --white:#fff;
}
*{margin:0;padding:0;box-sizing:border-box}
html,body{width:756px;height:1200px;overflow:hidden}
body{position:relative;font-family:"Lato",sans-serif;color:var(--text);background:var(--white)}
.abs{position:absolute}

/* header */
.site-header{position:absolute;left:0;top:0;width:756px;height:76px;background:var(--white)}
.brand{left:82px;top:18px;display:flex;align-items:center;gap:8px}
.brand-mark{width:34px;height:34px;border-radius:50%;background:var(--blue)}
.brand-name{font:900 20px/1 "Lato",sans-serif;color:var(--blue);letter-spacing:.3px}
.brand-tag{font:700 8.5px/1 "Lato",sans-serif;color:#555;letter-spacing:1.4px;margin-top:5px;text-align:center}
.award{top:8px;width:66px;text-align:center}
.award-badge{width:34px;height:44px;margin:0 auto;background:var(--badge);border-radius:3px}
.award-label{font:700 7.5px/1 "Lato",sans-serif;color:var(--blue);margin-top:8px}
.phone{left:562px;top:13px;display:flex;align-items:center;gap:6px;font:400 15px/1 "Lato",sans-serif;color:var(--red)}
.estimate-btn{left:540px;top:43px;width:134px;height:21px;background:linear-gradient(#1c86dc,#0a5fb3);border-radius:3px;color:var(--white);font:700 11px/21px "Lato",sans-serif;text-align:center}

/* nav */
.main-nav{position:absolute;left:0;top:76px;width:756px;height:30px;background:linear-gradient(var(--blue-nav-top),var(--blue-nav-bot))}
.main-nav ul{list-style:none;position:absolute;left:82px;top:0;display:flex;gap:11px}
.main-nav li{font:700 9.2px/30px "Lato",sans-serif;color:var(--white)}
.main-nav li.active{border-bottom:2px solid var(--white);line-height:27px}

/* hero */
.hero-bg{position:absolute;left:0;top:106px;width:756px;height:298px;background:var(--sky-light)}
.video{left:82px;top:106px;width:403px;height:227px;background:linear-gradient(135deg,#b8a48d,#d6c2a8 40%,#7f7d82);overflow:hidden}
.video-shade{position:absolute;left:0;bottom:17px;width:100%;height:90px;background:linear-gradient(rgba(0,0,0,0),rgba(0,0,0,.55))}
.play{left:186px;top:98px;width:30px;height:20px;background:var(--red);border-radius:4px}
.video-title{left:0;width:100%;top:156px;text-align:center;font:900 13px/1 "Lato",sans-serif;color:var(--blue)}
.video-sub{left:0;width:100%;top:176px;text-align:center;font:700 12.5px/1 "Open Sans",sans-serif;color:var(--white)}
.controls{left:0;bottom:0;width:100%;height:17px;background:linear-gradient(#3a3d44,#15171b)}
.progress{left:31px;top:6px;width:120px;height:4px;background:#ddd;border-radius:2px}
.time{left:156px;top:4px;font:400 6.5px/1 "Lato",sans-serif;color:#ddd}
.ctrl{top:3px;width:15px;height:11px;background:#5b6b85;border-radius:2px}
.callout{left:82px;top:333px;width:403px;height:71px;background:var(--blue-dark)}
.callout-text{left:14px;top:15px;width:228px;font:700 9px/13.5px "Roboto Condensed",sans-serif;color:var(--white)}
.callout-text b{color:var(--gold)}
.cred-box{left:245px;top:15px;width:146px;height:40px;background:var(--white);border-radius:4px}
.cred{top:5px;height:30px;border-radius:2px}

/* form */
.estimate-form{left:485px;top:106px;width:189px;height:298px;background:var(--form-red)}
.form-head{height:27px;background:var(--gold);font:700 12.5px/27px "Open Sans",sans-serif;color:#3a2a10;text-align:center}
.form-title{margin:5px 10px 0;font:700 11.5px/1.2 "Open Sans",sans-serif;color:var(--white)}
.form-intro{margin:2px 10px 0;font:400 7.2px/1.35 "Lato",sans-serif;color:#fbe7e7}
.field-label{display:block;margin:8px 10px 3px;font:400 7.5px/1 "Lato",sans-serif;color:var(--white)}
.field{margin:0 12px 0 10px;height:15px;background:var(--white);border-radius:2px}
.field.tall{height:35px}
.captcha{font:400 8px/15px "Lato",sans-serif;color:#333;padding-left:4px}
.submit{margin:7px 10px 0;width:59px;height:15px;background:var(--gold);border-radius:2px;font:700 8px/15px "Lato",sans-serif;color:var(--form-red);text-align:center}

/* welcome */
.welcome-bg{position:absolute;left:0;top:404px;width:756px;height:181px;background:linear-gradient(#e6f1fa,#cfe3f3)}
.welcome{left:82px;top:430px;width:592px;height:125px;background:var(--white);border:1px solid #d3dde6;border-radius:3px;box-shadow:0 6px 8px -6px rgba(0,0,0,.25)}
.welcome h1{position:absolute;left:13px;top:11px;font:700 12.5px/1 "Open Sans",sans-serif;color:var(--blue)}
.welcome h1 span{color:var(--red)}
.welcome p{position:absolute;left:13px;top:31px;width:566px;font:400 8.3px/14px "Open Sans",sans-serif;color:#555}

/* feature band */
.feature-band{position:absolute;left:0;top:585px;width:756px;height:347px;background:radial-gradient(ellipse at 50% 40%,#26324b,var(--navy-deep))}
.card{top:622px;height:262px}
.card h2{position:absolute;left:0;width:100%;top:12px;text-align:center;font:600 13px/16.5px "Open Sans",sans-serif;color:var(--white)}
.card .photo{position:absolute;left:8px;top:52px;width:154px;height:97px;background:var(--white);padding:6px}
.card .photo div{width:100%;height:100%}
.card p{position:absolute;left:10px;width:150px;top:158px;text-align:center;font:400 8px/13px "Open Sans",sans-serif;color:#1d1d1d;height:39px;overflow:hidden}
.card .more{position:absolute;left:0;width:100%;top:210px;text-align:center;font:700 8px/1 "Open Sans",sans-serif;color:#1d1d1d}
.card-orange{left:84px;width:176px;background:var(--orange)}
.card-cyan{left:291px;width:175px;background:var(--cyan)}
.card-green{left:495px;width:175px;background:var(--green)}

/* reviews */
.review-bg{position:absolute;left:0;top:932px;width:756px;height:206px;background:linear-gradient(#eaf4fb,#cfe2f2)}
.review-title{left:0;width:756px;top:953px;text-align:center;font:700 18px/1 "Open Sans",sans-serif;color:var(--blue)}
.review-title span{color:var(--red)}
.review-sub{left:0;width:756px;top:978px;text-align:center;font:400 9px/1 "Lato",sans-serif;color:#666}
.stars{left:0;width:756px;top:992px;text-align:center}
.divider{top:998px;height:1px;background:#b7c9d8}
.quote{left:82px;top:1017px;width:508px;height:62px;background:#f2f2f2;border-radius:3px;box-shadow:0 1px 2px rgba(0,0,0,.1)}
.quote p{position:absolute;left:15px;top:8px;width:470px;font:italic 400 8px/13px "Lato",sans-serif;color:#444}
.quote-mark{font:900 16px/1 "Lato",sans-serif;color:#aaa;margin-right:4px}
.avatar{left:588px;top:1014px;width:74px;height:74px;border-radius:50%;background:linear-gradient(#dfe6ec,#9aa7b3);border:3px solid var(--white);box-shadow:0 1px 4px rgba(0,0,0,.3)}
.reviewer{left:380px;width:209px;top:1092px;text-align:right;font:italic 700 8px/1 "Lato",sans-serif;color:#333}

/* footer */
.site-footer{position:absolute;left:0;top:1138px;width:756px;height:62px;background:var(--navy)}
.footer-nav{position:absolute;left:0;width:756px;top:21px;text-align:center;font:700 8px/1 "Lato",sans-serif;color:var(--white)}
.footer-nav span{margin:0 4px;color:#9aa}
.copyright{position:absolute;left:0;width:756px;top:37px;text-align:center;font:400 7.5px/1 "Lato",sans-serif;color:#bcc4d0}
</style>
</head>
<body>

<header class="site-header">
  <div class="abs brand">
    <div class="brand-mark"></div>
    <div>
      <div class="brand-name">CORVEL COATINGS</div>
      <div class="brand-tag">NOT JUST ANOTHER PAINTER</div>
    </div>
  </div>
  <div class="abs award" style="left:399px">
    <div class="award-badge" role="img" aria-label="Pellham Roster award badge"></div>
    <div class="award-label">Exterior Painting</div>
  </div>
  <div class="abs award" style="left:458px">
    <div class="award-badge" role="img" aria-label="Pellham Roster award badge"></div>
    <div class="award-label">Interior Painting</div>
  </div>
  <div class="abs phone">
    <svg width="15" height="15" viewBox="0 0 16 16" aria-hidden="true"><circle cx="8" cy="8" r="7" fill="none" stroke="#0d5fb0" stroke-width="1.4"/><path d="M5.2 4.3l1.4-.3.8 2-.9.7c.5 1 1.3 1.8 2.3 2.3l.7-.9 2 .8-.3 1.4c-3.2.2-6.2-2.8-6-6z" fill="#0d5fb0"/></svg>
    123 456 7890
  </div>
  <div class="abs estimate-btn">FREE ESTIMATES</div>
</header>

<nav class="main-nav">
  <ul>
    <li class="active">HOME</li><li>ABOUT US</li><li>RESIDENTIAL PAINTING</li><li>COMMERCIAL PAINTING</li><li>FAQ</li><li>SPECIALS</li><li>BLOG</li><li>TESTIMONIALS</li><li>CONTACT US</li>
  </ul>
</nav>

<div class="hero-bg"></div>
<section class="abs video" role="img" aria-label="Video still of a smiling child with colourful paint on her face">
  <div class="video-shade"></div>
  <div class="abs play"><svg width="30" height="20" viewBox="0 0 30 20" aria-hidden="true"><path d="M12 5l8 5-8 5z" fill="#fff"/></svg></div>
  <div class="abs video-title">CORVEL COATINGS</div>
  <div class="abs video-sub">RESIDENTIAL &amp; COMMERCIAL PAINTING COMPANY</div>
  <div class="abs controls">
    <div class="abs ctrl" style="left:6px"></div>
    <div class="abs progress"><div style="width:30px;height:4px;background:#8ab0d8;border-radius:2px"></div></div>
    <div class="abs time">1:47 / 12:05</div>
    <div class="abs ctrl" style="left:346px"></div>
    <div class="abs ctrl" style="left:364px"></div>
    <div class="abs ctrl" style="left:383px"></div>
  </div>
</section>
<section class="abs callout">
  <div class="abs callout-text">Need Painting In The Albuquerque Area?<br>Call Corvel Today For Your FREE Painting Estimate! <b>555-0147</b><br>Licensed - Bonded - Insured</div>
  <div class="abs cred-box">
    <div class="abs cred" style="left:6px;width:76px;background:#1f4a6b" role="img" aria-label="Accreditation badge"></div>
    <div class="abs cred" style="left:90px;width:50px;background:#cfd9e6" role="img" aria-label="Chamber of commerce badge"></div>
  </div>
</section>

<aside class="abs estimate-form">
  <div class="form-head">SCHEDULE FREE ESTIMATE</div>
  <div class="form-title">How to Schedule an Estimae</div>
  <div class="form-intro">Requesting an estimate online is very simple and easy. Fill out the Form below and we will send you a rough quote to your email. We may also call you if we have any more questions.</div>
  <span class="field-label">Name:</span><div class="field"></div>
  <span class="field-label">Email:</span><div class="field"></div>
  <span class="field-label">Phone:</span><div class="field"></div>
  <span class="field-label">Decribe what needs to be done.</span><div class="field tall"></div>
  <span class="field-label">Please type the following</span><div class="field captcha">ac2gH</div>
  <div class="submit">Submit Now</div>
</aside>

<div class="welcome-bg"></div>
<section class="abs welcome">
  <h1>Welcome To CORVEL <span>COATINGS</span></h1>
  <p>Corvel Coatings does jobs as small as a bathroom up to large commercial projects right here in Albuquerque and Rio Rancho. Extensive as an entire apartment exterior, to a kitchen and all home interior, no job is too big or too small for Corvel Coatings of Albuquerque. Corvel Coatings is staffed with the best painters for the highest quality paint jobs. Corvel Coatings is not a community's average house painter staffing company, but this painting company is staffed with professional painters that pride themselves on successfully completing every job.</p>
</section>

<div class="feature-band"></div>
<article class="abs card card-orange">
  <h2>Our Painting<br>In Albuquerque</h2>
  <div class="photo"><div role="img" aria-label="Photo of a couple painting a wall green" style="background:linear-gradient(120deg,#e8d9c8,#a9c66a)"></div></div>
  <p>Corvel Coatings does jobs as small as a bathroom up to large commercial projects right here in Albuquerque.</p>
  <div class="more">Read More ››</div>
</article>
<article class="abs card card-cyan">
  <h2>Albuquerque<br>Painter Videos</h2>
  <div class="photo"><div role="img" aria-label="Photo of a paint roller on an orange wall" style="background:linear-gradient(135deg,#e9a64a,#c7701a)"></div></div>
  <p>TWe have shot a ton of videos with Corvel answering all of your most frequently asked questions. We want</p>
  <div class="more">Read More ››</div>
</article>
<article class="abs card card-green">
  <h2>Happy Albuquerque<br>Painting Customers</h2>
  <div class="photo"><div role="img" aria-label="Photo of a person rolling light blue paint on a wall" style="background:linear-gradient(135deg,#d7ecf7,#7fb7dc)"></div></div>
  <p>100% Customer Satisfaction is our Ultimate Goal. We are proud to have served so many clients in an around</p>
  <div class="more">Read More ››</div>
</article>

<div class="review-bg"></div>
<h2 class="abs review-title">Our Customer <span>Review</span></h2>
<div class="abs review-sub">Lorem ipsum dolor sit amet, consectetur Donec a consequat mag Aenean eu velit Aenean sollicitudin</div>
<div class="abs divider" style="left:225px;width:132px"></div>
<div class="abs divider" style="left:400px;width:132px"></div>
<div class="abs stars">
  <svg width="32" height="9" viewBox="0 0 32 9" aria-hidden="true"><g fill="#f3a530"><path d="M4.5 0l1.1 3h3.2l-2.6 1.9 1 3.1-2.7-1.9L1.8 8l1-3.1L.2 3h3.2z"/><path transform="translate(11.5 0)" d="M4.5 0l1.1 3h3.2l-2.6 1.9 1 3.1-2.7-1.9L1.8 8l1-3.1L.2 3h3.2z"/><path transform="translate(23 0)" d="M4.5 0l1.1 3h3.2l-2.6 1.9 1 3.1-2.7-1.9L1.8 8l1-3.1L.2 3h3.2z"/></g></svg>
</div>
<blockquote class="abs quote">
  <p><span class="quote-mark">“</span>Lorem sum dolor sit amet, consectetuer adipiscing elit, sed diam nonummy nibh euismod tincidunt ut laoreet re agn aliqam erat volutpat wisi enim ad minim veniam, quis nostrud exerci tation ullamcorper suscipit lobortis nisl ut aliquip modo conseuatis autem vel eum iriure dolor in hendrerit in vulputate velit esse molestie consequat, vel illum dolore eu.</p>
</blockquote>
<div class="abs avatar" role="img" aria-label="Portrait photo of the reviewer"></div>
<div class="abs reviewer">Ravel Oskan, Northmere Group , USA</div>

<footer class="site-footer">
  <div class="footer-nav">HOME<span>|</span>ABOUT US<span>|</span>RESIDENTIAL PAINTING<span>|</span>COMMERCIAL PAINTING<span>|</span>FAQ<span>|</span>SPECIALS<span>|</span>BLOG<span>|</span>TESTIMONIALS<span>|</span>CONTACT US</div>
  <div class="copyright">© 2015 CORVEL COATINGS. ALL RIGHT RESERVED.</div>
</footer>

</body>
</html>
```